RTavenor Business Cards & Letterhead

I have a logo but need a design for some new business cards. We are a Design-Build Firm that specializes in the design and construction of commercial projects.
the cards need to be professional. no cartoon stuff.
i would like to have the cards in AI format so I can update the card as needed. Logo is provided.
Our Address is: 4187 Marlowe Ct. Brookfield, Vermont 27614

```html
<!DOCTYPE html>
<html lang="en">
<head>
<meta charset="utf-8">
<title>RTavenor Stationery</title>
<link rel="stylesheet" href="https://fonts.googleapis.com/css2?family=Open+Sans:wght@400;600;700;800&display=swap">
<style>
  :root {
    --bg: #d4d6d6;
    --paper: #ffffff;
    --brand-blue: #1a5a97;
    --brand-blue-dark: #0e3f70;
    --brand-grey: #6b6c70;
    --ink: #222326;
    --rule: #c9cbcd;
  }
  * { box-sizing: border-box; margin: 0; padding: 0; }
  html, body {
    width: 1200px; height: 686px; overflow: hidden;
    background: var(--bg);
    font-family: "Open Sans", sans-serif;
    color: var(--ink);
  }
  .canvas { position: relative; width: 1200px; height: 686px; }

  .sheet {
    position: absolute; background: var(--paper);
    box-shadow: 0 4px 14px rgba(0,0,0,.18);
  }

  /* Letterhead */
  .letterhead { left: 60px; top: 28px; width: 486px; height: 630px; }
  .wordmark {
    display: flex; align-items: center; gap: 8px;
    font-weight: 800; color: var(--brand-grey); letter-spacing: .5px;
    white-space: nowrap;
  }
  .wordmark .mark-square { background: var(--brand-blue); flex: none; }
  .letterhead .wordmark { position: absolute; top: 40px; right: 40px; font-size: 30px; }
  .letterhead .wordmark .mark-square { width: 22px; height: 22px; }

  .letterhead-footer { position: absolute; left: 40px; right: 40px; bottom: 36px; }
  .footer-rule { position: relative; height: 2px; background: var(--brand-blue-dark); margin-bottom: 12px; }
  .footer-rule .rule-square {
    position: absolute; left: 50%; top: -6px; width: 14px; height: 14px;
    margin-left: -7px; background: var(--brand-blue);
  }
  .contact-row { display: flex; gap: 16px; font-size: 11.5px; align-items: center; white-space: nowrap; }
  .contact-item { display: flex; align-items: center; gap: 5px; }
  .contact-item svg { width: 11px; height: 11px; flex: none; }
  .footer-address { font-size: 11.5px; margin-top: 6px; white-space: nowrap; }

  /* Business cards */
  .card { width: 520px; height: 297px; left: 620px; }
  .card-front { top: 28px; display: flex; }
  .card-back { top: 361px; display: flex; align-items: center; justify-content: center; }

  .card-brand {
    width: 230px; display: flex; align-items: center; justify-content: center;
  }
  .card-brand .wordmark { color: var(--brand-blue); font-size: 26px; }
  .card-brand .mark-square { width: 20px; height: 20px; }
  .card-divider { width: 1px; background: var(--rule); margin: 60px 0 40px; }
  .card-details { padding: 64px 0 0 30px; font-size: 11.5px; line-height: 1.55; white-space: nowrap; }
  .person-name { color: var(--brand-blue); font-weight: 700; font-size: 17px; letter-spacing: .5px; }
  .person-role { font-weight: 600; margin-bottom: 10px; }
  .card-details .contact-item { margin-top: 2px; }

  .card-back .wordmark { font-size: 38px; }
  .card-back .mark-square { width: 28px; height: 28px; }
</style>
</head>
<body>
<div class="canvas">

  <section class="sheet letterhead">
    <div class="wordmark"><span class="mark-square"></span>RTAVENOR</div>
    <footer class="letterhead-footer">
      <div class="footer-rule"><span class="rule-square"></span></div>
      <div class="contact-row">
        <span class="contact-item">
          <svg viewBox="0 0 12 12"><path fill="#1a5a97" d="M2.5 1h2l1 2.5-1.3 1a6 6 0 0 0 3.3 3.3l1-1.3L11 7.5v2c0 .8-.7 1.5-1.5 1.5A8.5 8.5 0 0 1 1 2.5C1 1.7 1.7 1 2.5 1z"/></svg>
          (802) 555-0148
        </span>
        <span class="contact-item">
          <svg viewBox="0 0 12 12"><rect x="1" y="2.5" width="10" height="7" rx="1" fill="#1a5a97"/><path d="M1.5 3l4.5 3.5L10.5 3" stroke="#fff" fill="none"/></svg>
          RMT@RTavenor.com
        </span>
        <span class="contact-item">
          <svg viewBox="0 0 12 12"><circle cx="6" cy="6" r="5" fill="#1a5a97"/><path d="M1 6h10M6 1c-2 2.5-2 7.5 0 10M6 1c2 2.5 2 7.5 0 10" stroke="#fff" stroke-width=".8" fill="none"/></svg>
          www.rtavenor.com
        </span>
      </div>
      <p class="footer-address">4187 Marlowe Ct. Brookfield, Vermont 27614</p>
    </footer>
  </section>

  <section class="sheet card card-front">
    <div class="card-brand">
      <div class="wordmark"><span class="mark-square"></span>RTAVENOR</div>
    </div>
    <div class="card-divider"></div>
    <div class="card-details">
      <p class="person-name">ROWAN TAVENOR</p>
      <p class="person-role">Founder/President</p>
      <p>4187 Marlowe Ct. Brookfield,<br>Vermont 27614</p>
      <p class="contact-item">
        <svg viewBox="0 0 12 12"><path fill="#1a5a97" d="M2.5 1h2l1 2.5-1.3 1a6 6 0 0 0 3.3 3.3l1-1.3L11 7.5v2c0 .8-.7 1.5-1.5 1.5A8.5 8.5 0 0 1 1 2.5C1 1.7 1.7 1 2.5 1z"/></svg>
        (802) 555-0148
      </p>
      <p class="contact-item">
        <svg viewBox="0 0 12 12"><circle cx="6" cy="6" r="5" fill="#1a5a97"/><path d="M1 6h10M6 1c-2 2.5-2 7.5 0 10M6 1c2 2.5 2 7.5 0 10" stroke="#fff" stroke-width=".8" fill="none"/></svg>
        www.rtavenor.com
      </p>
      <p class="contact-item">
        <svg viewBox="0 0 12 12"><rect x="1" y="2.5" width="10" height="7" rx="1" fill="#1a5a97"/><path d="M1.5 3l4.5 3.5L10.5 3" stroke="#fff" fill="none"/></svg>
        RMT@RTavenor.com
      </p>
    </div>
  </section>

  <section class="sheet card card-back">
    <div class="wordmark"><span class="mark-square"></span>RTAVENOR</div>
  </section>

</div>
</body>
</html>
```